Flyer for handout on the street to attract people

Create two different leaflets for handing out to recruit volunteers to participate in a program of biological specimen donation. The leaflet should be catchy, have some graphics, and have enough info that people will want to sign up by going to the website for more information.

Leave room on each leaflet for some English and Chinese. The example of Leaflet #1 will need approximately the same space in order to have the Chinese translation.

The example of Leaflet #2 already has a Chinese translation which can be incorporated.

The size should be half of A4 page. If it is a whole A4 page it may also be considered.

Leaflet #1 Text:

RECRUITING HEALTHY VOLUNTEERS (and get PAID)!

The Orient Floracell Reserve is recruiting healthy individuals in Hong Kong to participate in a scientific research project to study bacteria in healthy guts. They will pay you $200 HKD per day to participate in the study. If you qualify, you can earn up to $4800 a month!

Incidences of digestive and colon diseases are increasing rapidly in Hong Kong, and part of the key to solving this problem is understanding gut bacteria. There are up to 100 trillion bacteria and microbes in every human gut, including yours. Scientists have recently uncovered that these bacteria are key human digestion and immune systems. However, when your gut bacteria are imbalanced, it can cause all kinds of problems such as indigestion, IBS, ulcerative colitis, or clostridium difficile infection.

Every year, more than 500,000 people are infected by a toxic bacteria called clostridium difficile, which causes severe stomach pain, and sometimes even death. YOUR GUT BACTERIA COULD BE KEY TO HELPING THESE SICK PATIENTS.

CRITERIA FOR PARTICIPATING: If you are a healthy adult between 18-50 years old; no digestive problems and no recent medications, then the Orient VitaVault needs your participation! They will pay you $200 HKD per day to participate in the study. If you qualify, you can earn up to $4800 a month! To learn more information, go to http://www.orientvitavault.example or send a whatsapp to 7342 9086

Leaflet #2 Text:

Get paid to give your poopoo!

Literally.

Asia’s first commercial stool bank is recruiting donors. Get paid up to $4,800 HKD per month for your poop donations at our convenient Central Hong Kong lab.

Answer the questionnaire to see if you qualify at www.orientvitavault.example or call 7342 9086 for more information.

你好屎!

我地就係想要你D好屎。

全亞洲第一間商業糞便銀行正招募捐贈者。請即前往我們位於中環的糞便銀行成為捐贈者,每月最多可賺取6,000港元的酬勞。

想知道自己是否適合捐贈?馬上點擊 www.orientvitavault.example/donate 回答問題或撥打0000-0000查詢詳情。

Target Market(s)

Young professionals, middle-class

Industry/Entity Type

Medical

Font styles to use
Serif
Sans Serif
Decorative

Requirements
Must have
• The text. Two leaflet examples. Some graphics.
Nice to have
• Catchy design. Something people will see while walking past and go ahead and take it from someone handing out flyers.
Should not have
• Only text. Should be colorful and have graphics. (Can download or shutterstock photos.)

```html
<!DOCTYPE html>
<html lang="en">
<head>
<meta charset="utf-8">
<title>Orient Floracell Reserve – Volunteer Leaflet</title>
<link href="https://fonts.googleapis.com/css2?family=Fjalla+One&family=Open+Sans:wght@400;600;700&display=swap" rel="stylesheet">
<style>
  :root{
    --stage:#e8e8ea;
    --paper:#ffffff;
    --paper-shade:#eef0f4;
    --royal:#1d3fd8;
    --ring:#6f88f2;
    --ink:#1c1c22;
    --ink-soft:#33343c;
    --photo-a:#dfe8f3;
    --photo-b:#b9cbe2;
  }
  *{box-sizing:border-box;margin:0;padding:0}
  html,body{width:1200px;height:1200px;overflow:hidden;background:var(--stage)}
  body{font-family:"Open Sans",Arial,sans-serif;color:var(--ink)}
  .page{position:absolute;left:50px;width:1100px;height:540px;background:var(--paper);box-shadow:0 6px 22px rgba(0,0,0,.18);overflow:hidden}
  .page--front{top:40px}
  .page--back{top:620px;background:linear-gradient(180deg,#fff 0%,var(--paper-shade) 100%)}
  .shapes{position:absolute;inset:0;width:100%;height:100%}

  /* front page */
  .headline{position:absolute;left:40px;top:40px;font-family:"Fjalla One",Impact,sans-serif;line-height:.95;text-transform:uppercase}
  .headline span{display:block}
  .headline .l1{font-size:36px;color:var(--ink)}
  .headline .l2{font-size:50px;color:var(--royal)}
  .headline .l3{font-size:36px;color:var(--ink)}
  .headline .l4{font-size:32px;color:var(--royal)}
  .brand{position:absolute;left:270px;top:70px;display:flex;align-items:center;gap:10px;font-weight:600;font-size:22px;color:var(--royal)}
  .brand .dot{width:30px;height:30px;border-radius:50%;background:var(--royal)}
  .body-copy{position:absolute;left:40px;top:245px;width:520px;font-size:13px;line-height:1.45;color:var(--ink-soft)}
  .body-copy p{margin-bottom:12px}
  .callout{color:var(--royal);text-transform:uppercase;letter-spacing:.08em}
  .team-photo{position:absolute;right:0;top:0;width:420px;height:200px;background:linear-gradient(135deg,var(--photo-a),var(--photo-b))}
  .criteria{position:absolute;right:40px;top:215px;width:340px;text-align:right}
  .criteria h2{font-family:"Fjalla One",Impact,sans-serif;font-size:28px;line-height:1;color:var(--royal);text-transform:uppercase;margin-bottom:12px}
  .criteria ul{list-style:none;font-size:12.5px;line-height:1.4;color:var(--ink-soft)}
  .criteria li{position:relative;padding-right:18px;margin-bottom:3px}
  .criteria li::after{content:"";position:absolute;right:0;top:6px;width:8px;height:8px;border-radius:50%;background:var(--royal)}
  .criteria .contact{margin-top:14px;font-size:12.5px;line-height:1.5;color:var(--ink-soft)}
  .criteria .contact a{color:var(--royal);text-decoration:none}

  /* back page */
  .circle-photo{position:absolute;border-radius:50%;border:9px solid var(--ring);background:linear-gradient(135deg,var(--photo-a),var(--photo-b))}
  .circle-photo--one{left:60px;top:40px;width:210px;height:210px}
  .circle-photo--two{left:330px;top:40px;width:230px;height:230px}
  .circle-photo--three{left:620px;top:40px;width:200px;height:200px}
  .device-photo{position:absolute;right:40px;top:40px;width:220px;height:190px;background:linear-gradient(135deg,#d7dde6,#9aa6b8)}
  .pitch{position:absolute;left:60px;top:284px;width:520px;font-weight:700;font-size:16px;line-height:1.5;color:var(--ink)}
  .pitch em{font-style:normal;color:var(--royal)}
  .cta{position:absolute;right:40px;bottom:36px;width:440px;text-align:right;font-weight:700;font-size:20px;line-height:1.35;color:#fff}
</style>
</head>
<body>

<section class="page page--front" aria-label="Leaflet one: recruiting healthy volunteers">
  <svg class="shapes" viewBox="0 0 1100 540" preserveAspectRatio="none" aria-hidden="true">
    <path d="M0 225 C180 205 420 190 560 130 C620 100 660 60 680 0 L700 0 C690 75 640 125 580 160 C440 230 200 235 0 240Z" fill="var(--royal)"/>
    <path d="M680 0 C700 120 760 190 860 205 L1100 205 L1100 200 L870 198 C780 185 715 110 700 0Z" fill="var(--royal)"/>
    <path d="M700 540 L1100 505 L1100 517 L740 540Z" fill="var(--royal)"/>
  </svg>

  <h1 class="headline">
    <span class="l1">Recruiting</span>
    <span class="l2">Healthy</span>
    <span class="l3">Volunteers</span>
    <span class="l4">And get paid</span>
  </h1>

  <div class="brand"><span class="dot"></span>Orient Floracell Reserve</div>

  <div class="team-photo" role="img" aria-label="Photo of smiling medical staff in white coats"></div>

  <div class="body-copy">
    <p>The Orient Floracell Reserve is recruiting healthy individuals in Hong Kong to participate in a scientific research project to study bacteria in healthy guts. They will pay you $200 HKD per day to participate in the study. If you qualify, you can earn up to $4800 a month!</p>
    <p>Incidences of digestive and colon diseases are increasing rapidly in Hong Kong, and part of the key to solving this problem is understanding gut bacteria. There are up to 100 trillion bacteria and microbes in every human gut, including yours. Scientists have recently uncovered that these bacteria are key human digestion and immune systems. However, when your gut bacteria are imbalanced, it can cause all kinds of problems such as indigestion, IBS, ulcerative colitis, or clostridium difficile infection.</p>
    <p>Every year, more than 500,000 people are infected by a toxic bacteria called clostridium difficile, which causes severe stomach pain, and sometimes even death.</p>
    <p class="callout">Your gut bacteria could be key to helping these sick patients.</p>
  </div>

  <div class="criteria">
    <h2>Criteria for<br>participating</h2>
    <ul>
      <li>If you are a healthy adult between 18-50 years old;</li>
      <li>No digestive problems and no recent medications,</li>
      <li>Then the Orient VitaVault needs your participation!</li>
      <li>They will pay you $200 HKD per day to participate in the study.</li>
      <li>If you qualify, you can earn up to $4800 a month!</li>
    </ul>
    <p class="contact"><a href="http://www.orientvitavault.example">To learn more information, go to www.orientvitavault.example</a><br>or send a whatsapp to 7342 9086</p>
  </div>
</section>

<section class="page page--back" aria-label="Leaflet two: stool bank donors">
  <svg class="shapes" viewBox="0 0 1100 540" preserveAspectRatio="none" aria-hidden="true">
    <path d="M0 515 C260 495 500 375 680 315 C840 265 980 255 1100 250 L1100 540 L0 540Z" fill="#f3f4f8"/>
    <path d="M0 540 C260 520 500 400 680 340 C840 290 980 280 1100 275 L1100 540Z" fill="var(--royal)"/>
  </svg>

  <div class="circle-photo circle-photo--one" role="img" aria-label="Photo of a doctor reviewing notes with a patient"></div>
  <div class="circle-photo circle-photo--two" role="img" aria-label="Photo of a smiling team of medical staff"></div>
  <div class="circle-photo circle-photo--three" role="img" aria-label="Photo of doctors consulting over a clipboard"></div>
  <div class="device-photo" role="img" aria-label="Photo of a hand holding a tablet showing a medical cross"></div>

  <p class="pitch">Asia's first commercial stool bank is recruiting donors. Get paid up to <em>$4,800 HKD</em> per month for your poop donations at our convenient Central Hong Kong lab.</p>

  <p class="cta">Answer the questionnaire to see if you qualify at www.orientvitavault.example or call 7342 9086 for more information.</p>
</section>

</body>
</html>
```